Local Flower Farm Needs Business Card Design

I need business cards designed for a flower farm based in Eudora, Kansas.
Business Info:
We are a local cut flower farm located in Eudora, Kansas, founded by Corinne Haldwick. What started as a passion for agriculture and search for more joy in daily life has blossomed into a small business dedicated to providing the community with beautiful, fresh, and sustainable flowers. We specialize in local, seasonal blooms, ensuring that every petal reflects the care and dedication we pour into our craft. Our mission is to deliver the highest quality flowers directly to our customers through local farmers markets and to florists who share our commitment to sustainability. Join us in celebrating the beauty of nature, one bloom at a time!
Contact Details:
Corinne Haldwick
Owner
Phone 913-555-0147
Facebook: Rosalind Thorpe Gardens
Instagram: @RosalindThorpeGardens
Website: RosalindThorpeGardens.example
Target Market(s)
Wholesale to Florists and Direct to Consumer via Farmers Market
Industry/Entity Type
Florist, Farm
Contact Information for Business Card
Name, Contact Info, Logo
Look and feel
Each slider illustrates characteristics of the customer's brand and the style your logo design should communicate.

```html
<!DOCTYPE html>
<html lang="en">
<head>
<meta charset="utf-8">
<title>Rosalind Thorpe Gardens – Business Card</title>
<link rel="stylesheet" href="https://fonts.googleapis.com/css2?family=Libre+Baskerville:wght@400;700&display=swap">
<style>
  :root {
    --page: #e4e8e9;
    --ink: #0b252b;
    --paper: #ffffff;
    --mint: #8fcaa4;
    --mint-deep: #2f6a5c;
    --text-dark: #111a1c;
  }
  * { box-sizing: border-box; margin: 0; padding: 0; }
  html, body { width: 1200px; height: 960px; overflow: hidden; }
  body {
    background: var(--page);
    font-family: "Libre Baskerville", "Times New Roman", serif;
    position: relative;
  }
  .card { position: absolute; overflow: hidden; }

  /* Front */
  .card-front {
    left: 245px; top: 58px; width: 710px; height: 405px;
    background: var(--ink);
  }
  .pattern-field {
    position: absolute; inset: 0;
    background:
      radial-gradient(ellipse 70% 75% at 100% 0%, rgba(143,202,164,0.55) 0%, rgba(47,106,92,0.35) 45%, rgba(11,37,43,0) 80%),
      linear-gradient(180deg, #0f2e33 0%, var(--ink) 100%);
  }
  .front-name {
    position: absolute; left: 560px; top: 290px; width: 130px;
    color: var(--paper); font-size: 11px; line-height: 1.3; text-align: center;
  }

  /* Back */
  .card-back {
    left: 249px; top: 500px; width: 702px; height: 400px;
    background: var(--paper);
  }
  .brand-seal {
    position: absolute; left: 265px; top: 27px; width: 166px; height: 166px;
    border: 1px solid var(--ink); border-radius: 50%;
    display: flex; align-items: center; justify-content: center;
    text-align: center; color: var(--ink);
    font-size: 17px; line-height: 1.35; font-weight: 700;
  }
  .contact-band {
    position: absolute; left: 0; top: 242px; width: 702px; height: 94px;
    background: var(--ink); color: var(--paper);
  }
  .owner {
    position: absolute; left: 22px; top: 15px; width: 268px; text-align: right;
  }
  .owner-name { font-size: 24px; font-weight: 700; letter-spacing: 0.5px; }
  .owner-role { font-size: 16px; margin-top: 2px; }
  .band-brand {
    position: absolute; left: 302px; top: 24px; width: 104px;
    font-size: 13px; line-height: 1.35; text-align: center;
  }
  .contact-list {
    position: absolute; left: 414px; top: 12px; list-style: none;
    font-size: 16px; line-height: 24px; letter-spacing: 0.3px;
  }
  .contact-list li { display: flex; align-items: center; gap: 9px; }
  .contact-list svg { width: 17px; height: 17px; flex: none; }
  .website {
    position: absolute; left: 0; top: 352px; width: 702px; text-align: center;
    font-size: 16px; color: var(--text-dark); letter-spacing: 0.3px;
  }
</style>
</head>
<body>

<section class="card card-front">
  <div class="pattern-field" role="img" aria-label="Repeating brand monogram pattern with soft green foil gradient in the upper right"></div>
  <div class="front-name">Rosalind Thorpe Gardens</div>
</section>

<section class="card card-back">
  <div class="brand-seal">Rosalind<br>Thorpe<br>Gardens</div>

  <div class="contact-band">
    <div class="owner">
      <div class="owner-name">Corinne Haldwick</div>
      <div class="owner-role">Owner</div>
    </div>

    <div class="band-brand">Rosalind Thorpe Gardens</div>

    <ul class="contact-list">
      <li>
        <svg viewBox="0 0 24 24" aria-hidden="true"><path fill="#fff" d="M6.6 10.8a15.1 15.1 0 0 0 6.6 6.6l2.2-2.2c.3-.3.7-.4 1-.2 1.1.4 2.3.6 3.6.6.6 0 1 .4 1 1V20c0 .6-.4 1-1 1C10.6 21 3 13.4 3 4c0-.6.4-1 1-1h3.5c.6 0 1 .4 1 1 0 1.3.2 2.5.6 3.6.1.3 0 .7-.2 1l-2.3 2.2z"/></svg>
        913-555-0147
      </li>
      <li>
        <svg viewBox="0 0 24 24" aria-hidden="true"><circle cx="12" cy="12" r="10" fill="#fff"/></svg>
        Rosalind Thorpe Gardens
      </li>
      <li>
        <svg viewBox="0 0 24 24" aria-hidden="true"><rect x="3" y="3" width="18" height="18" rx="4" fill="none" stroke="#fff" stroke-width="2"/></svg>
        @RosalindThorpeGardens
      </li>
    </ul>
  </div>

  <div class="website">RosalindThorpeGardens.example</div>
</section>

</body>
</html>
```